Zielgruppe
Beamer Vermietung
Aufgabenstellung
Erstellung 2 professionell aussehender Webseiten.
Projektor-Verleih-Raum-Ostlingen.de
sowie
Projektor-Verleih-Raum-Wendbergshof.de
Die Seiten sind aktuell im Betrieb, aber haben ein sehr veraltetes Design.
Die Seiten können ähnlich aussehen, sollten aber etwas unterschiedlich sein, damit sie für den Kunden leicht anders aussehen.
Wichtig ist, dass alle Seiten, inklusive Startseite, Unterseiten und Links designed werden und das dieses Design in die bestehende Wordpress Installation eingepflegt wird.
Es ist also notwendig, gute Wordpress Kenntnisse zu haben um dann auch zwei fertige Wordpress Seiten liefern zu können.

```html
<!DOCTYPE html>
<html lang="de">
<head>
<meta charset="utf-8">
<title>Projektor-Verleih Raum Ostlingen</title>
<link href="https://fonts.googleapis.com/css2?family=Roboto:wght@300;400;500;700;900&family=Roboto+Condensed:wght@400&display=swap" rel="stylesheet">
<style>
:root{
  --slate:#4e6466;
  --sage:#7b9e9a;
  --light:#efefef;
  --topbar:#ebebeb;
  --text:#4b5a5c;
  --muted:#5f6b6d;
  --white:#ffffff;
}
*{margin:0;padding:0;box-sizing:border-box}
html,body{width:763px;height:1200px;overflow:hidden}
body{position:relative;font-family:"Roboto",sans-serif;background:var(--white);color:var(--text)}
.abs{position:absolute}
.topbar{left:0;top:0;width:763px;height:20px;background:var(--topbar);border-bottom:1px solid #d6d6d6}
.topbar .url{left:103px;top:5px;font-size:7px;color:#444}
.social{top:5px;width:10px;height:10px;border-radius:50%;background:var(--slate)}
.header{left:0;top:20px;width:763px;height:44px;background:var(--white)}
.site-title{left:101px;top:30px;font-family:"Roboto Condensed",sans-serif;font-size:18px;color:var(--slate)}
.header-links{top:36px;font-size:8.5px;font-weight:500;color:var(--slate)}
.nav{left:0;top:64px;width:763px;height:31px;background:var(--slate)}
.nav ul{position:absolute;left:103px;top:0;display:flex;list-style:none;height:31px}
.nav li{font-size:9.5px;font-weight:500;color:var(--white);line-height:31px;padding:0 5px}
.nav li.active{background:var(--sage);padding:0 7px}
.hero{left:0;top:95px;width:763px;height:293px;background:linear-gradient(100deg,#6d7778 0%,#b7b8b6 35%,#cfcdc8 60%,#a9a8a4 100%)}
.hero-rule{left:102px;top:162px;width:18px;height:2px;background:var(--slate)}
.hero-title{left:102px;top:167px;font-size:30px;line-height:35px;font-weight:700;color:var(--white)}
.hero-sub{left:102px;top:238px;font-size:16px;font-weight:500;color:var(--white)}
.btn-kontakt{left:103px;top:295px;width:90px;height:23px;border-radius:12px;background:var(--white);color:#111;font-size:9px;font-weight:700;text-align:center;line-height:23px}
.band{left:0;top:388px;width:763px;height:53px;background:var(--light)}
.dot-big{left:73px;top:412px;width:16px;height:16px;border-radius:50%;background:var(--slate)}
.dot-small{left:94px;top:404px;width:7px;height:7px;border-radius:50%;background:var(--sage)}
.band-text{left:113px;top:404px;font-size:17.5px;font-weight:700;color:var(--slate);white-space:nowrap}
.price{display:inline-block;width:38px;height:38px;border-radius:50%;background:var(--slate);color:var(--white);text-align:center;line-height:38px;vertical-align:middle;margin-top:-10px}
.intro{left:0;top:460px;width:763px;text-align:center;font-size:18.5px;font-weight:300;line-height:24px;color:var(--text)}
.offer h2{font-size:22px;font-weight:500;color:var(--slate);line-height:27px}
.offer p{font-weight:300;color:var(--muted);white-space:nowrap}
.offer .l1{font-size:23px;line-height:28px}
.btn-more{display:inline-block;margin-top:10px;width:71px;height:24px;border-radius:12px;background:var(--slate);color:var(--white);font-size:9px;text-align:center;line-height:24px}
.product{border-radius:10px}
.cta{left:0;top:1063px;width:763px;height:108px;background:linear-gradient(120deg,#4b5f61,#5f7577 50%,#526769)}
.cta-title{left:100px;top:1100px;font-size:26px;font-weight:500;color:var(--white)}
.cta-phone{left:453px;top:1106px;font-size:21px;font-weight:300;color:var(--white);display:flex;align-items:center;gap:10px}
.footer{left:0;top:1171px;width:763px;height:29px;background:var(--sage);text-align:center;font-size:7.5px;color:var(--white);line-height:29px}
</style>
</head>
<body>
<div class="abs topbar"><span class="abs url">www.projektor-verleih-raum-ostlingen.de</span>
  <span class="abs social" style="left:589px"></span><span class="abs social" style="left:608px"></span><span class="abs social" style="left:627px"></span><span class="abs social" style="left:646px"></span>
</div>
<div class="abs header"></div>
<div class="abs site-title">Beamer Vermietung zu Günstigen Konditionen</div>
<div class="abs header-links" style="left:516px;display:flex;align-items:center;gap:5px">
  <svg width="13" height="9" viewBox="0 0 13 9"><rect x="0.5" y="0.5" width="12" height="8" fill="none" stroke="#4e6466"/><path d="M0.5 0.5 L6.5 5 L12.5 0.5" fill="none" stroke="#4e6466"/></svg>
  Kontakt / Anreise</div>
<div class="abs header-links" style="left:616px">Impressum</div>
<nav class="abs nav"><ul>
  <li class="active">Startseite</li><li>Beamer mieten</li><li>HD-Beamer mieten</li><li>Full HD-Beamer</li><li>Leinwand mieten</li><li>Reservierung</li><li>Preisliste</li><li>Datenschutz</li>
</ul></nav>
<div class="abs hero" role="img" aria-label="Foto eines Beamers auf einem Holztisch vor unscharfem Seminarraum"></div>
<div class="abs hero-rule"></div>
<h1 class="abs hero-title">&nbsp;! Beamer mieten zu<br>TOP-Konditionen !</h1>
<div class="abs hero-sub">NEU: Jetzt auch HD-Beamer!</div>
<div class="abs btn-kontakt">KONTAKT</div>
<div class="abs band"></div>
<div class="abs dot-big"></div><div class="abs dot-small"></div>
<div class="abs band-text">Beamer-Vermietung im Raum Ostlingen / Kelbrück &nbsp;für nur<span class="price">€30</span>/ Tag</div>
<div class="abs intro">Jetzt neu: HD-Beamer für das<br>perfekte Bilderlebnis zu günstigen Konditionen!</div>

<div class="abs offer" style="left:104px;top:554px">
  <h2>Beamer mieten</h2>
  <p class="l1">Informationen zum Modell:<br>Beamer Modell Kestrel KX-310</p>
  <span class="btn-more" style="margin-left:-1px">Weiterlesen</span>
</div>
<div class="abs product" style="left:448px;top:538px;width:215px;height:148px;background:radial-gradient(ellipse at center,#6a6d70 0%,#b9bbbd 55%,#fff 80%)" role="img" aria-label="Produktfoto eines dunkelgrauen Beamers"></div>

<div class="abs product" style="left:103px;top:710px;width:207px;height:100px;background:radial-gradient(ellipse at center,#c4c6c8 0%,#e3e4e5 55%,#fff 80%)" role="img" aria-label="Produktfoto eines silbernen HD-Beamers"></div>
<div class="abs offer" style="left:338px;top:715px">
  <h2>HD Beamer mieten</h2>
  <p class="l1">Informationen zum Modell:</p>
  <p style="font-size:21px;line-height:26px">HD-Beamer Modell Varnel Lumo 4</p>
  <span class="btn-more" style="margin-left:1px">Weiterlesen</span>
</div>

<div class="abs offer" style="left:104px;top:872px">
  <h2>Full-HD Beamer mieten</h2>
  <p class="l1">Informationen zum Modell:</p>
  <p style="font-size:18px;line-height:26px">Full-HD-Beamer Modell Solvano S-88 Pro</p>
  <span class="btn-more" style="margin-left:-1px">Weiterlesen</span>
</div>
<div class="abs product" style="left:443px;top:868px;width:220px;height:122px;background:radial-gradient(ellipse at center,#c9cacc 0%,#e6e7e8 55%,#fff 80%)" role="img" aria-label="Produktfoto eines weißen Full-HD-Beamers"></div>

<div class="abs cta"></div>
<h3 class="abs cta-title">Reservieren oder Buchen</h3>
<div class="abs cta-phone">
  <svg width="22" height="16" viewBox="0 0 22 16"><path d="M1 5 Q11 -2 21 5 L19 8 L15 6 L15 4 Q11 2.5 7 4 L7 6 L3 8 Z" fill="#fff"/><path d="M6 7 L16 7 L19 15 L3 15 Z" fill="#fff"/><circle cx="11" cy="11" r="2.3" fill="#526769"/></svg>
  Tel: 0151 / 2840617</div>
<div class="abs footer">Copyright © 2020.&nbsp; Projektor-verleih-raum-ostlingen.de</div>
</body>
</html>
```